Holzdesign Firma sucht stilvolles Corporate Design
Zielgruppe
Ich stelle Utensilien aus Holz für die Küche her und verkaufe diese übers Internet. In erster Linie platzsparende Messerbretter aus Holz. Meine Zielgruppe ist jeder in Deutschland der eine Küche hat und dort kocht.
Aufgabenstellung
Das Design sollte eher schlicht und innovativ wirken. Der Name FELSGART muss mit ihm Logo sein. Im Logo sollte auch eine Verbindung zum Holz erkennbar sein, am besten mit einem Holzbalken oder einem Baumstamm. Im Logo sollen keine Weihnachtsbäume oder ganze Bäume sichtbar sein. Die Farbwahl würde ich auf Farben die zu Holz und Natur passen eingrenzen.
Mit dem Design will ich mich von den übrigen Handwerksbetrieben abheben und nicht einfach die üblichen Standarddesigns kopieren.

```html
<!DOCTYPE html>
<html lang="de">
<head>
<meta charset="utf-8">
<title>FELSGART – Geschäftsausstattung</title>
<link href="https://fonts.googleapis.com/css2?family=Barlow:wght@300;400;600;700&display=swap" rel="stylesheet">
<style>
:root{
  --wood:#4a2a17;
  --wood-mark:#5a3011;
  --ink:#2f2f2f;
  --label:#8a8a8a;
  --paper:#ffffff;
  --stage-a:#fafafa;
  --stage-b:#e9e9e9;
  --shadow:0 6px 14px rgba(0,0,0,.18);
}
*{margin:0;padding:0;box-sizing:border-box}
html,body{width:1200px;height:801px;overflow:hidden}
body{
  position:relative;
  background:radial-gradient(ellipse at 35% 20%,var(--stage-a),var(--stage-b));
  font-family:"Barlow",sans-serif;color:var(--ink);
}
.abs{position:absolute}
.brand-square{background:var(--wood-mark)}
.wordmark{font-weight:700;color:var(--wood-mark);letter-spacing:.06em;white-space:nowrap;line-height:1}
.slogan{color:var(--wood-mark);white-space:nowrap;line-height:1}

/* main logo */
.hero-square{left:307px;top:82px;width:44px;height:44px}
.hero-wordmark{left:235px;top:187px;width:186px;text-align:center;font-size:30px}
.hero-slogan{left:235px;top:220px;width:186px;text-align:center;font-size:12.4px;letter-spacing:.05em}

.piece-label{top:263px;width:260px;text-align:center;font-size:15.5px;font-weight:300;color:var(--label)}

/* business cards */
.card{background:var(--paper);box-shadow:var(--shadow);overflow:hidden}
.card-front{left:58px;top:292px;width:259px;height:167px}
.card-front .brand-square{position:absolute;left:114px;top:42px;width:30px;height:30px}
.card-front .wordmark{position:absolute;left:0;width:100%;top:108px;text-align:center;font-size:17px}
.card-front .slogan{position:absolute;left:0;width:100%;top:128px;text-align:center;font-size:6.2px;letter-spacing:.04em}
.card-back{left:333px;top:293px;width:260px;height:168px}
.card-back .wordmark{position:absolute;left:0;width:100%;top:43px;text-align:center;font-size:15px}
.card-back .band{position:absolute;left:0;right:0;top:98px;bottom:0;background:var(--wood);color:#fff;text-align:center}
.card-back .holder{margin-top:13px;font-weight:700;font-size:12.5px;letter-spacing:.06em}
.card-back .contact{font-size:8.4px;letter-spacing:.04em;line-height:12.6px;margin-top:2px}

/* envelope */
.envelope{left:58px;top:496px;width:536px;height:268px;background:var(--paper);box-shadow:var(--shadow)}
.envelope .wordmark{position:absolute;left:96px;top:52px;font-size:15px}
.envelope .window{position:absolute;left:47px;top:121px;width:206px;height:111px;border-radius:12px;background:linear-gradient(135deg,#a8a8a8,#b5b5b5 60%,#9d9d9d)}

/* letterhead */
.letter{left:630px;top:34px;width:521px;height:737px;background:var(--paper);box-shadow:var(--shadow);font-size:7px;line-height:10.4px}
.letter .brand-square{position:absolute;left:247px;top:22px;width:26px;height:26px}
.letter .wordmark{position:absolute;left:0;width:100%;top:88px;text-align:center;font-size:16px}
.letter .slogan{position:absolute;left:0;width:100%;top:106px;text-align:center;font-size:6.2px;letter-spacing:.04em}
.sender-line{position:absolute;left:63px;top:157px;font-size:5.4px;white-space:nowrap}
.sender-line b,.sender-block b,.footer b{font-weight:700;letter-spacing:.05em}
.recipient{position:absolute;left:63px;top:175px;line-height:12.3px}
.sender-block{position:absolute;right:32px;top:135px;text-align:right;font-size:6.3px;line-height:10.4px}
.sender-block p+p{margin-top:7.5px}
.letter-body{position:absolute;left:63px;top:245px;width:420px}
.letter-body p{margin-bottom:10.6px}
.letter-body .subject{margin-bottom:21px}
.fold{position:absolute;left:0;height:1px;background:var(--wood)}
.footer{position:absolute;left:0;right:0;bottom:0;height:72px;background:var(--wood);color:#e9ded5;font-size:6.2px;line-height:10.4px}
.footer .col{position:absolute;top:21px}
.footer b{color:#fff}
</style>
</head>
<body>

<section class="brand-mark" aria-label="Logo">
  <div class="abs brand-square hero-square"></div>
  <div class="abs wordmark hero-wordmark">FELSGART</div>
  <div class="abs slogan hero-slogan">Hier könnte Ihr Slogan stehen.</div>
</section>

<div class="abs piece-label" style="left:57px">Visitenkarte vorne</div>
<div class="abs piece-label" style="left:332px">Visitenkarte hinten</div>

<div class="abs card card-front">
  <div class="brand-square"></div>
  <div class="wordmark">FELSGART</div>
  <div class="slogan">Hier könnte Ihr Slogan stehen.</div>
</div>

<div class="abs card card-back">
  <div class="wordmark">FELSGART</div>
  <div class="band">
    <div class="holder">JONAS WEIDLER</div>
    <div class="contact">Lärchenweg 5 | 45868 Tannbrück | Tel.: 0251 739264<br>j.weidler@felsgart.de | www.felsgart.de</div>
  </div>
</div>

<div class="abs envelope">
  <div class="wordmark">FELSGART</div>
  <div class="window"></div>
</div>

<article class="abs letter">
  <div class="brand-square"></div>
  <div class="wordmark">FELSGART</div>
  <div class="slogan">Hier könnte Ihr Slogan stehen.</div>

  <div class="sender-line"><b>FELSGART</b> | Lärchenweg 9 | 45868 Tannbrück</div>
  <div class="recipient">Herr Brandlmeier<br>Birkenstraße 3<br>48555 Grünau</div>

  <div class="sender-block">
    <p><b>FELSGART</b><br>Ahornallee 93a<br>55555 Eichfeld</p>
    <p>Tel.: 0251 739264<br>Fax: 0251 739265<br>Mobil: 0172 4815906</p>
    <p>info@felsgart.de<br>www.felsgart.de</p>
  </div>

  <div class="fold" style="top:261px;width:8px"></div>
  <div class="fold" style="top:369px;width:15px"></div>
  <div class="fold" style="top:521px;width:8px"></div>

  <div class="letter-body">
    <p class="subject">Hier steht eine Betreffzeile</p>
    <p>Sehr geehrte Frau Ostrowski,</p>
    <p>als Kunde unseres jungen und modernen Unternehmens erwartet<br>Sie Qualität in höchstem Maße.</p>
    <p>Sie können sicher zu sein, genau zu bekommen, was wir Ihnen versprechen.<br>Und damit werden Sie auch rundum zufrieden sein. Das garantieren wir Ihnen.</p>
    <p>Schauen Sie doch gleich das beiliegende Prospekt. Wir bieten Ihnen moderne und hochwertige Produkte, die auf dem neuesten Stand der Technik sind, an. Überzeugen Sie sich selbst von der hochwertigen Qualität unserer Produkte und bestellen Sie noch heute.</p>
    <p>Wir freuen uns auf Ihre Bestellung und sind bei Rückfragen gerne für Sie da.</p>
    <p>Mit freundlichen Grüßen</p>
  </div>

  <footer class="footer">
    <div class="col" style="left:50px"><b>FELSGART</b><br>Lärchenweg 9<br>45868 Tannbrück</div>
    <div class="col" style="left:189px">USt-IDNR: DE7264019<br>Steuernummer: 174/318/206<br>Inhaber: Jonas Weidler</div>
    <div class="col" style="left:365px">Kreisbank Lindental<br>IBAN: DE27 4031 0000 0000 8153<br>BIC: KBLDXXX21</div>
  </footer>
</article>

</body>
</html>
```